LED strip light bag design

We are brivolta lighting, a LED strip manufacturer in China, We need a packaging design for our LED strip light, as the strip market is full of standard package, so we want to make our package special, and use color orange, black and grey

Target Market(s)

USA, Europe

Contact Information for Business Card

Mason Walsh
Director
Shenzhen Brivolta Lighting Co., Ltd.
Add: 3F, Kaiwen Ind. Zone, Dapu Rd, Hexing, Shenzhen 518207 China
Tel: +86-139-4820 6637 Fax: +86-755-28493016
E-mail: mason.walsh@brivolta-example.com

Font styles to use
Sans Serif
Other font styles liked:
• Tw Cen MT Condensed

Colors

Designer to choose only greyscale colors for use in the design.

Requirements
Must have
• Must have instructions of how to use the strip and CAUTION
• Must have CE, RoHS UL, trash can, ISO9001 logo
Nice to have
• Nice to have a back ground pictures with a strip drawing.

```html
<!DOCTYPE html>
<html lang="en">
<head>
<meta charset="utf-8">
<title>Brivolta LED Strip Light Bag</title>
<link href="https://fonts.googleapis.com/css2?family=Jost:wght@400;500;600;700&display=swap" rel="stylesheet">
<style>
  :root {
    --orange: #f58634;
    --white: #ffffff;
    --frame-grey: #6d6e70;
    --ink: #231f20;
    --badge: #3a3a3c;
    --photo-light: #f7f7f7;
    --photo-mid: #d9d6d2;
  }
  * { margin: 0; padding: 0; box-sizing: border-box; }
  html, body { width: 1075px; height: 1200px; overflow: hidden; background: var(--orange); }
  .bag {
    position: relative; width: 1075px; height: 1200px;
    background: var(--orange); border: 1px solid #5a3a22;
    font-family: 'Jost', sans-serif; color: var(--white);
  }
  .website { position: absolute; right: 46px; top: 52px; font-size: 32px; letter-spacing: 1px; font-weight: 400; }
  .brand-title { position: absolute; left: 50px; top: 58px; display: flex; align-items: flex-start; }
  .brand-title .big { font-size: 118px; font-weight: 600; line-height: 0.82; letter-spacing: 2px; }
  .brand-title .stack { margin-left: 8px; font-size: 50px; font-weight: 400; line-height: 0.92; letter-spacing: 9px; }
  .title-rule { position: absolute; left: 48px; width: 262px; height: 2px; background: var(--white); }
  .title-band { position: absolute; left: 48px; top: 180px; width: 262px; height: 18px; background: rgba(255,255,255,0.25); }
  .corner { position: absolute; left: 0; top: 0; }
  .photo-frame { position: absolute; left: 27px; top: 239px; }
  .chip-band { position: absolute; left: 0; top: 769px; width: 1075px; height: 48px; background: rgba(255,255,255,0.18); }
  .chip-band::before, .chip-band::after { content: ""; position: absolute; left: 0; width: 1075px; height: 3px; background: var(--white); }
  .chip-band::before { top: 0; } .chip-band::after { bottom: 0; }
  .caution { position: absolute; left: 134px; top: 896px; color: var(--ink); }
  .caution h2 { font-size: 27px; font-weight: 600; }
  .caution p { font-size: 27px; font-weight: 400; line-height: 1.27; text-transform: uppercase; }
  .caution-icon { position: absolute; left: 48px; top: 937px; }
  .attention { position: absolute; left: 618px; top: 872px; width: 440px; }
  .attention h3 { font-size: 24px; font-weight: 600; margin-bottom: 10px; }
  .attention ul { list-style: none; font-size: 16.5px; line-height: 1.35; }
  .attention li { margin-bottom: 13px; padding-left: 12px; text-indent: -12px; }
  .attention li::before { content: "• "; }
  .badges { position: absolute; left: 128px; top: 1076px; }
</style>
</head>
<body>
<div class="bag">
  <div class="brand-title">
    <span class="big">LED</span>
    <span class="stack">STRIP<br>LIGHT</span>
  </div>
  <svg class="corner" width="1075" height="1200" aria-hidden="true">
    <polyline points="556,62 572,62 572,84" fill="none" stroke="#fff" stroke-width="5"/>
  </svg>
  <div class="title-rule" style="top:172px"></div>
  <div class="title-band" role="img" aria-label="Row of LED chip motifs"></div>
  <div class="title-rule" style="top:202px"></div>
  <div class="website">www.brivolta.com</div>

  <svg class="photo-frame" width="1022" height="502" viewBox="0 0 1022 502">
    <defs>
      <linearGradient id="photoTone" x1="0" y1="0" x2="1" y2="1">
        <stop offset="0" stop-color="var(--photo-light)"/>
        <stop offset="0.55" stop-color="var(--photo-mid)"/>
        <stop offset="1" stop-color="var(--photo-light)"/>
      </linearGradient>
    </defs>
    <path d="M0 0 H955 A67 67 0 0 1 1022 67 V502 H165 A165 165 0 0 1 0 337 Z" fill="var(--frame-grey)"/>
    <path role="img" aria-label="Photo of a reel of warm white LED strip light" d="M13 13 H950 A58 58 0 0 1 1008 71 V488 H168 A155 155 0 0 1 13 333 Z" fill="url(#photoTone)"/>
  </svg>

  <div class="chip-band" role="img" aria-label="Row of LED chip motifs"></div>

  <svg class="caution-icon" width="62" height="56" viewBox="0 0 62 56" aria-hidden="true">
    <path d="M31 3 L59 52 H3 Z" fill="var(--ink)" stroke="var(--ink)" stroke-width="5" stroke-linejoin="round"/>
    <rect x="28" y="18" width="6" height="20" rx="2" fill="#fff"/>
    <circle cx="31" cy="45" r="3.5" fill="#fff"/>
  </svg>
  <div class="caution">
    <h2>CAUTION</h2>
    <p>This bag contents<br>moisture and electrostatic<br>sensitive devices</p>
  </div>

  <div class="attention">
    <h3>Attention</h3>
    <ul>
      <li>Storage Temperature 40+80C<br>Operating Temperature 25--60C</li>
      <li>Installation surface must be smooth clean and dry.</li>
      <li>The part of LED components can not be fixed on the surface of the sharp edge.</li>
      <li>Strip should not be collided or crushed.</li>
      <li>Strip can be cut following the cutting lines.</li>
      <li>The LED strips, must not exceed 5 meters, when used in a DC series circuit.</li>
    </ul>
  </div>

  <svg class="badges" width="270" height="100" viewBox="0 0 270 100" role="img" aria-label="Certification marks">
    <circle cx="30" cy="58" r="30" fill="var(--badge)"/>
    <circle cx="123" cy="58" r="30" fill="var(--badge)"/>
    <rect x="190" y="20" width="60" height="76" fill="var(--badge)"/>
  </svg>
</div>
</body>
</html>
```